WE ARE BRIGHT SPARROW, building a full website with ecommerce

requirements:
CODED FOR SITEQUILL
ONLINE STORE FUNCTION WITH E-COMMERCE USING TRADEBLOOM
PAGEWAVE AND PICTOLANE LINKS

I need a website design for my organization, WE ARE BRIGHT SPARROW, a global empowerment movement elevating woman, and the world. The site's home page should reflect our mission, to empower women. It should have a strong, empowering feel, with minimalistic design.
Please see www.lunavelto.com and http://www.corvenhal.co/ for an inspiration on layout and feel.

**PLEASE SEE ATTACHMENT "LOGO MOCK UP" FOR LOGO. THIS IS NOT THE FINAL VECTOR FILE, BUT THIS LOOKS THE SAME AS THE FINAL LOGO.

HOME PAGE:
The first section of the home page should include a background image with our logo center.

You should include the following links to pages at the top right of the page:
MISSION
MANTRA
ARMOR
MEET BS (I would like "bs" to be our logo)
pagewave and pictolane links

As you scroll down the page, you should see the following sections, which correlate to the links to pages as written above. **SEE ATTACHED SKETCH "HOMEPAGE LAYOUT IDEA" FOR REFERENCE**

WHO WE ARE (correlates to the link Mission)

OUR MANTRA (correlates to the link Mantra)

OUR ARMOR (correlates to the link The Shirt)
(This is where we will sell a shirt (and other apparel) and need the e-commerce function)

MEET BRIGHT SPARROWS (correlates to the link Meet BS)

SHOW OFF YOUR SUPER POWERS (correlates to the pagewave and pictolane)

FEATURED BRIGHT SPARROW (no link on top right of page)

On the homepage, for each of the above sections, as you scroll down there should be an image, either in the background or framed, next to the title (WHO WE ARE, for example), as well as one sentence of small text explaining the title. The title (WHO WE ARE) and the one sentence should link to a page (ie WHO WE ARE + the one sentence links to the MISSION page). ** SEE ATTACHED SKETCH "HOMEPAGE SECTION IDEAS" FOR REFERENCE**

**PLEASE SEE ATTACHMENT "WEBSITE TITLE IDEAS" FOR A STARTING PLACE OF THE LOOK. These don't have to be exact, but they give you an idea of what I'm looking for.

**FONTS TYPOLD EXTRA BOLD AND TYPOLD BOOK 500 (WHICH SHOULD BE BOLDED MANUALLY) ARE ATTACHED**

Target Market(s)

Women, mainly in US

Industry/Entity Type

Social

Coding

Coded - Design and coding required

Number of Pages Required

5+ page

Font styles to use
Other font styles liked:
• Typol Extra Bold

Requirements
Must have
• CODED FOR SITEQUILL
• ONLINE STORE FUNCTION WITH E-COMMERCE USING TRADEBLOOM
• PAGEWAVE AND PICTOLANE LINKS
• Typold Extra Bold and Typold Book 500, attached
• please see description for all requirements
Nice to have
• please see description for all ideas
Should not have

```html
<!DOCTYPE html>
<html lang="en">
<head>
<meta charset="utf-8">
<title>We Are Bright Sparrow</title>
<link href="https://fonts.googleapis.com/css2?family=Montserrat:wght@300;400;500;700;800&display=swap" rel="stylesheet">
<style>
:root{
  --orange:#f4714f;
  --orange-deep:#ee6241;
  --dark:#232323;
  --ink:#111111;
  --white:#ffffff;
  --muted:#8a8a8a;
}
*{box-sizing:border-box;margin:0;padding:0}
html,body{width:1200px;height:3502px;overflow:hidden;background:var(--white)}
body{font-family:"Montserrat",Arial,sans-serif;color:var(--white);position:relative}

/* brand mark: invented name beside one plain square */
.mark{display:flex;align-items:center;justify-content:center;border:4px solid currentColor;font-weight:800;letter-spacing:1px;flex:none}

/* header */
.site-header{position:absolute;top:0;left:0;width:1200px;height:89px;background:var(--white);border-top:6px solid var(--ink)}
.brand{position:absolute;left:163px;top:21px;display:flex;align-items:center;gap:9px;color:var(--ink)}
.brand .mark{width:38px;height:38px;border-width:3px;font-size:13px}
.brand-name{font-weight:800;font-size:11px;line-height:12px;letter-spacing:.4px}
.main-nav{position:absolute;left:560px;top:36px;display:flex;gap:46px;font-size:12px;font-weight:500;color:var(--ink);letter-spacing:.6px}
.social-links{position:absolute;left:968px;top:30px;display:flex;gap:12px}
.social-link{display:flex;align-items:center;gap:5px;font-size:9px;font-weight:700;color:var(--ink);letter-spacing:.4px}
.social-dot{width:26px;height:26px;border-radius:50%;background:var(--orange)}

/* hero */
.hero{position:absolute;top:89px;left:0;width:1200px;height:513px;overflow:hidden}
.hero-photo{position:absolute;inset:0;background:
  radial-gradient(ellipse 180px 230px at 330px 230px,#a88f80 0%,rgba(168,143,128,0) 100%),
  radial-gradient(ellipse 160px 220px at 520px 220px,#8d7466 0%,rgba(141,116,102,0) 100%),
  radial-gradient(ellipse 170px 230px at 720px 220px,#4a3a34 0%,rgba(74,58,52,0) 100%),
  radial-gradient(ellipse 180px 240px at 910px 230px,#6b5a58 0%,rgba(107,90,88,0) 100%),
  radial-gradient(ellipse 300px 120px at 600px 470px,#5a3a2c 0%,rgba(90,58,44,0) 100%),
  linear-gradient(180deg,#8c7f76 0%,#6f645d 45%,#514a46 100%)}
.hero-light{position:absolute;inset:0;background:linear-gradient(90deg,rgba(30,26,24,.45) 0%,rgba(30,26,24,.2) 60%,rgba(235,232,228,.35) 100%)}
.hero-mark{position:absolute;left:560px;top:114px;width:80px;height:80px;font-size:24px}
.hero-title{position:absolute;top:208px;left:0;width:1200px;text-align:center;font-size:27px;line-height:38px}
.hero-title strong{font-weight:800;display:block;letter-spacing:.5px}
.hero-title span{font-weight:400;letter-spacing:.6px}
.signup{position:absolute;left:337px;top:300px;width:528px;height:38px;display:flex}
.signup-field{flex:1;background:var(--white);color:var(--muted);font-size:12px;line-height:38px;padding-left:14px;border-radius:3px 0 0 3px}
.signup-button{width:102px;background:var(--orange);color:var(--white);font-size:11px;font-weight:700;line-height:38px;text-align:center;border-radius:0 19px 19px 0}
.slider-dots{position:absolute;top:456px;left:560px;display:flex;gap:8px}
.slider-dots i{width:14px;height:14px;border-radius:50%;background:var(--white)}
.slider-dots i.active{background:var(--orange)}

/* intro band */
.intro-band{position:absolute;top:602px;left:0;width:1200px;height:176px;background:linear-gradient(90deg,var(--orange) 0%,#f67d5a 50%,var(--orange) 100%)}
.intro-text{position:absolute;top:19px;width:1200px;text-align:center;font-size:20px;line-height:31px;font-weight:400;letter-spacing:.4px}
.intro-text strong{font-weight:800}
.cta-fly{position:absolute;left:536px;top:97px;display:flex;align-items:center;gap:10px}
.cta-fly .mark{width:46px;height:46px;border-width:3px;font-size:14px}
.cta-label{font-weight:800}
.cta-label small{display:block;font-size:18px;line-height:19px}
.cta-label b{display:block;font-size:32px;line-height:32px}

/* feature sections */
.feature{position:absolute;left:0;width:1200px;overflow:hidden}
.feature-photo{position:absolute;inset:0}
.feature-panel{position:absolute;inset:0}
.panel-dark{background:linear-gradient(180deg,#262626 0%,#1f1f1f 100%)}
.panel-orange{background:linear-gradient(160deg,#f67a57 0%,var(--orange) 50%,var(--orange-deep) 100%)}
.feature-copy{position:absolute;width:360px;font-size:12.5px;line-height:22px;font-weight:400}
.feature-price{display:block;margin-top:30px;font-weight:700;font-size:16px}
.feature-heading{position:absolute;display:flex;align-items:center;gap:20px}
.feature-heading.right{flex-direction:row-reverse;text-align:right}
.feature-heading .mark{width:80px;height:80px;border-width:5px;font-size:24px}
.heading-text{font-weight:800;font-size:40px;line-height:47px;text-transform:uppercase}

.who{top:778px;height:444px}
.mantra{top:1222px;height:443px}
.meet{top:1665px;height:439px}
.armor{top:2104px;height:444px}
.superpowers{top:2548px;height:441px}
.featured{top:2989px;height:443px}

.shirt-print{position:absolute;left:738px;top:274px;display:flex;align-items:center;gap:6px;color:rgba(255,255,255,.45);font-size:9px;font-weight:800;line-height:10px}
.shirt-print i{width:20px;height:20px;border:2px solid rgba(255,255,255,.45)}

.social-diamonds{position:absolute;left:735px;top:150px;display:flex;gap:34px}
.social-diamond{display:flex;flex-direction:column;align-items:center;gap:26px;font-size:11px;font-weight:700;letter-spacing:.5px}
.social-diamond i{width:72px;height:72px;border:4px solid var(--white);transform:rotate(45deg);margin-top:16px}

/* footer */
.site-footer{position:absolute;top:3432px;left:0;width:1200px;height:70px;background:var(--ink);font-size:11px;letter-spacing:.5px;color:#d8d8d8}
.site-footer p{position:absolute;top:30px;width:1200px;text-align:center}
.site-footer span{margin-left:16px}
</style>
</head>
<body>

<header class="site-header">
  <div class="brand">
    <div class="mark">BS</div>
    <div class="brand-name">WE ARE<br>BRIGHT<br>SPARROW</div>
  </div>
  <nav class="main-nav">
    <span>MISSION</span><span>MANTRA</span><span>MEET BS</span><span>ARMOR</span>
  </nav>
  <div class="social-links">
    <span class="social-link"><i class="social-dot"></i>PAGEWAVE</span>
    <span class="social-link"><i class="social-dot"></i>PICTOLANE</span>
  </div>
</header>

<section class="hero">
  <div class="hero-photo" role="img" aria-label="Group of four women smiling together around a table in a bright office"></div>
  <div class="hero-light"></div>
  <div class="mark hero-mark">BS</div>
  <h1 class="hero-title"><strong>WE ARE BRIGHT SPARROW</strong><span>AND I WILL CONQUER THE WORLD</span></h1>
  <div class="signup">
    <div class="signup-field">hello@brightsparrow.org</div>
    <div class="signup-button">LET'S FLY</div>
  </div>
  <div class="slider-dots"><i></i><i class="active"></i><i></i><i></i></div>
</section>

<section class="intro-band">
  <p class="intro-text"><strong>WE ARE BRIGHT SPARROW</strong> IS A GLOBAL EMPOWERMENT<br>MOVEMENT ELEVATING WOMEN... AND THE WORLD.</p>
  <div class="cta-fly">
    <div class="mark">BS</div>
    <div class="cta-label"><small>LET'S</small><b>FLY</b></div>
  </div>
</section>

<section class="feature who">
  <div class="feature-photo" role="img" aria-label="Smiling woman with curly hair in a dark navy blouse" style="background:
    radial-gradient(ellipse 170px 200px at 390px 330px,#1f2a3e 0%,rgba(31,42,62,0) 100%),
    radial-gradient(ellipse 120px 150px at 380px 120px,#5a3c2e 0%,rgba(90,60,46,0) 100%),
    radial-gradient(ellipse 60px 200px at 20px 300px,#7a5a48 0%,rgba(122,90,72,0) 100%),
    linear-gradient(90deg,#b9b2ab 0%,#d6d1cc 45%,#c4bfbb 100%)"></div>
  <div class="feature-panel panel-dark" style="clip-path:polygon(540px 0,1200px 0,1200px 100%,695px 100%)"></div>
  <div class="feature-heading" style="left:163px;top:130px">
    <div class="mark">BS</div>
    <div class="heading-text">Who<br>we<br>are</div>
  </div>
  <p class="feature-copy" style="left:693px;top:165px">Lorem ipsum dolor sit amet, consectetur adipiscing elit sed do eiusmod tempor incididunt ut labore et dolore mag na aliquat enim ad minim veniamuis.</p>
</section>

<section class="feature mantra">
  <div class="feature-photo" role="img" aria-label="Smiling woman with long dark hair in a coral top beside a colleague in black" style="background:
    radial-gradient(ellipse 150px 170px at 1040px 380px,#c97a60 0%,rgba(201,122,96,0) 100%),
    radial-gradient(ellipse 140px 150px at 720px 380px,#1e1614 0%,rgba(30,22,20,0) 100%),
    radial-gradient(ellipse 130px 200px at 960px 170px,#3a221a 0%,rgba(58,34,26,0) 100%),
    linear-gradient(90deg,#6e4434 0%,#5a3427 55%,#4a2a20 100%)"></div>
  <div class="feature-panel panel-orange" style="clip-path:polygon(0 0,700px 0,550px 100%,0 100%)"></div>
  <p class="feature-copy" style="left:163px;top:176px">Lorem ipsum dolor sit amet, consectetur adipiscing elit sed do eiusmod tempor incididunt ut labore et dolore mag na aliquat enim ad minim veniamuis.</p>
  <div class="feature-heading right" style="right:163px;top:160px">
    <div class="mark">BS</div>
    <div class="heading-text">Our<br>Mantra</div>
  </div>
</section>

<section class="feature meet">
  <div class="feature-photo" role="img" aria-label="Woman working on a laptop at a wooden desk by a large window with plants" style="background:
    radial-gradient(ellipse 260px 70px at 260px 370px,#5a4634 0%,rgba(90,70,52,0) 100%),
    radial-gradient(ellipse 90px 150px at 470px 230px,#d8d2cc 0%,rgba(216,210,204,0) 100%),
    radial-gradient(ellipse 80px 70px at 70px 300px,#5f6a3a 0%,rgba(95,106,58,0) 100%),
    linear-gradient(180deg,#3e4a3a 0%,#56584a 45%,#3a3430 100%)"></div>
  <div class="feature-panel panel-dark" style="clip-path:polygon(553px 0,1200px 0,1200px 100%,700px 100%)"></div>
  <div class="feature-heading" style="left:163px;top:130px">
    <div class="mark">BS</div>
    <div class="heading-text">Meet<br>Bright<br>Sparrows</div>
  </div>
  <p class="feature-copy" style="left:693px;top:160px">Lorem ipsum dolor sit amet, consectetur adipiscing elit sed do eiusmod tempor incididunt ut labore et dolore mag na aliquat enim ad minim veniamuis.</p>
</section>

<section class="feature armor">
  <div class="feature-photo" role="img" aria-label="Smiling woman wearing the navy movement shirt with arms crossed" style="background:
    radial-gradient(ellipse 200px 200px at 850px 340px,#1c2438 0%,rgba(28,36,56,0) 100%),
    radial-gradient(ellipse 110px 130px at 850px 110px,#5a3a2c 0%,rgba(90,58,44,0) 100%),
    linear-gradient(90deg,#8a8684 0%,#6e6c70 50%,#b5b1ad 100%)"></div>
  <div class="feature-panel panel-orange" style="clip-path:polygon(0 0,700px 0,560px 100%,0 100%)"></div>
  <p class="feature-copy" style="left:163px;top:143px">Lorem ipsum dolor sit amet, consectetur adipiscing elit sed do eiusmod tempor incididunt ut labore et dolore mag na aliquat enim ad minim veniamuis.<span class="feature-price">$ 89.00</span></p>
  <div class="shirt-print"><i></i><span>BRIGHT<br>SPARROW</span></div>
  <div class="feature-heading right" style="right:163px;top:150px">
    <div class="mark">BS</div>
    <div class="heading-text">Our<br>Armor</div>
  </div>
</section>

<section class="feature superpowers">
  <div class="feature-photo" role="img" aria-label="Group of laughing women posing close together" style="background:
    radial-gradient(ellipse 130px 150px at 120px 200px,#c49a80 0%,rgba(196,154,128,0) 100%),
    radial-gradient(ellipse 130px 150px at 330px 160px,#d0a88e 0%,rgba(208,168,142,0) 100%),
    radial-gradient(ellipse 120px 140px at 560px 360px,#c69c84 0%,rgba(198,156,132,0) 100%),
    radial-gradient(ellipse 200px 120px at 300px 30px,#5a3a28 0%,rgba(90,58,40,0) 100%),
    linear-gradient(90deg,#6e4a36 0%,#8e6a56 50%,#7a5e50 100%)"></div>
  <div class="feature-panel panel-dark" style="clip-path:polygon(560px 0,1200px 0,1200px 100%,712px 100%)"></div>
  <div class="feature-heading" style="left:163px;top:135px">
    <div class="mark">BS</div>
    <div class="heading-text">Show off<br>your super<br>powers</div>
  </div>
  <div class="social-diamonds">
    <div class="social-diamond"><i></i><span>PAGEWAVE</span></div>
    <div class="social-diamond"><i></i><span>PICTOLANE</span></div>
  </div>
</section>

<section class="feature featured">
  <div class="feature-photo" role="img" aria-label="Woman speaking to a seated group in a bright studio" style="background:
    radial-gradient(ellipse 110px 220px at 1070px 230px,#3a3436 0%,rgba(58,52,54,0) 100%),
    radial-gradient(ellipse 160px 110px at 800px 380px,#8a7a6e 0%,rgba(138,122,110,0) 100%),
    radial-gradient(ellipse 120px 90px at 700px 60px,#5c6e7a 0%,rgba(92,110,122,0) 100%),
    linear-gradient(90deg,#9a9896 0%,#b8b6b2 55%,#cfccc8 100%)"></div>
  <div class="feature-panel panel-orange" style="clip-path:polygon(0 0,712px 0,560px 100%,0 100%)"></div>
  <p class="feature-copy" style="left:163px;top:176px">Lorem ipsum dolor sit amet, consectetur adipiscing elit sed do eiusmod tempor incididunt ut labore et dolore mag na aliquat enim ad minim veniamuis.</p>
  <div class="feature-heading right" style="right:163px;top:125px">
    <div class="mark">BS</div>
    <div class="heading-text">Featured<br>Bright<br>Sparrow</div>
  </div>
</section>

<footer class="site-footer">
  <p>© COPYRIGHT 2017 . ALL RIGHTS RESERVED.<span>PRIVACY</span><span>TERMS OF USE</span><span>COOKIES</span></p>
</footer>

</body>
</html>
```